CopperWanderer Stretching and Strength

We need a application design for a our first IOS application. the goal of the application is to categorize stretching and strength routines for triathlon.

We would like to see designs that use the color orange.

The design of the application should be compliant with the last version of the IOS Mobile.

For this first design we need the folowing pages:

1- Sign up
2- Log in
3- Home
4- View Exercises
5- Do it
6- Profile

The description of each page is in the attached document.

We need a logo design for the application. The logo should express that mission of the application that is for stretch and strength training for Triathlon.

We will use https://pellavokit.example to develop the application, if you have any experience of the limitation that this technology have it will be a plus.

If you have any question please feel free to contact us.

Reason: We will extend the deadline to be sure that we select the best design from all of you. we will take the final decision next Tuesday.

Target Market(s)

The market for my aplicación is the Running a Triathlon world.

Logo Text

CopperWanderer

Font styles to use
Serif

Colors
f37122
ffffff
dcdcdc

Requirements
Must have
• In some future we will add more features in the menu. We should considere it for the design.
• The designs should include all the screens in the power point.

```html
<!DOCTYPE html>
<html lang="en">
<head>
<meta charset="utf-8">
<title>CopperWanderer – Home</title>
<link href="https://fonts.googleapis.com/css2?family=Roboto:wght@400;500&display=swap" rel="stylesheet">
<style>
  :root {
    --orange: #f37122;
    --orange-light: #fba26c;
    --white: #ffffff;
    --canvas: #d6e3ef;
    --surface: #ececec;
    --line: #dcdcdc;
    --text: #444444;
    --muted: #777777;
  }
  * { box-sizing: border-box; margin: 0; padding: 0; }
  html, body {
    width: 1200px; height: 1200px; overflow: hidden;
    background: var(--canvas);
    font-family: "Roboto", sans-serif;
    color: var(--text);
  }
  .screen {
    position: absolute; left: 270px; top: 9px;
    width: 660px; height: 1182px;
    background: var(--surface);
    overflow: hidden;
  }
  .status-bar {
    position: absolute; left: 0; top: 0; width: 100%; height: 46px;
    background: var(--orange); color: var(--white);
    font-size: 19px;
  }
  .status-bar .carrier { position: absolute; left: 8px; top: 12px; display: flex; align-items: center; gap: 6px; }
  .status-bar .signal { letter-spacing: 1px; font-size: 14px; }
  .status-bar .clock { position: absolute; left: 0; right: 0; top: 12px; text-align: center; }
  .status-bar .battery { position: absolute; right: 10px; top: 12px; display: flex; align-items: center; gap: 6px; }
  .app-header {
    position: absolute; left: 0; top: 46px; width: 100%; height: 72px;
    background: var(--orange); color: var(--white);
    display: flex; align-items: center; justify-content: center;
    font-size: 27px; font-weight: 500; letter-spacing: 0.5px;
  }
  .app-header .menu-toggle { position: absolute; left: 15px; top: 26px; }
  .card {
    position: absolute; left: 16px; width: 629px;
    background: var(--white);
    box-shadow: 0 1px 3px rgba(0,0,0,0.12);
    overflow: hidden;
  }
  .chart-card { top: 139px; height: 352px; }
  .range-tabs { position: absolute; top: 16px; left: 0; width: 100%; font-size: 18px; color: var(--muted); }
  .range-tabs span { position: absolute; transform: translateX(-50%); white-space: nowrap; }
  .range-tabs .active { color: var(--orange); }
  .chart-card svg { position: absolute; left: 0; top: 0; }
  .total-routines {
    position: absolute; top: 308px; width: 100%; text-align: center;
    font-size: 20px; font-weight: 500; color: #333;
  }
  .total-routines em { font-style: normal; color: var(--orange); }
  .history-card { top: 505px; height: 463px; }
  .section-title { font-size: 22px; font-weight: 500; color: #333; }
  .history-head { position: absolute; left: 27px; right: 28px; top: 16px; display: flex; align-items: center; gap: 10px; }
  .history-head .rule { flex: 1; height: 1px; background: var(--line); }
  .history-head .see-more { color: var(--orange); font-size: 18px; font-weight: 500; }
  .history-list { position: absolute; left: 0; top: 73px; width: 100%; list-style: none; }
  .history-item { position: relative; height: 88px; }
  .history-item .activity-icon { position: absolute; left: 18px; top: 20px; }
  .history-item p {
    position: absolute; left: 91px; top: 14px; width: 420px;
    font-size: 21px; line-height: 29px; color: var(--text);
  }
  .history-item time { position: absolute; right: 14px; top: 16px; font-size: 16px; color: var(--muted); }
  .history-item::after {
    content: ""; position: absolute; left: 91px; right: 0; bottom: 0; height: 1px; background: var(--line);
  }
  .history-item.faded { opacity: 0.45; }
  .history-fade {
    position: absolute; left: 0; bottom: 0; width: 100%; height: 40px;
    background: linear-gradient(rgba(255,255,255,0), var(--white));
  }
  .sponsors-card { top: 983px; height: 176px; }
  .sponsors-card .section-title { position: absolute; left: 27px; top: 17px; }
  .sponsor-row { position: absolute; left: 20px; top: 62px; display: flex; gap: 10px; }
  .sponsor-tile {
    width: 188px; height: 101px; border: 1px solid var(--line);
    display: flex; align-items: center; justify-content: center; gap: 8px;
    font-size: 22px; font-weight: 500; color: #222;
  }
  .sponsor-tile .mark { width: 14px; height: 14px; background: #222; border-radius: 50%; }
</style>
</head>
<body>
<main class="screen">
  <div class="status-bar">
    <div class="carrier">
      <span class="signal">●●●○○</span><span>KESTREL</span>
      <svg width="20" height="16" viewBox="0 0 20 16" aria-hidden="true">
        <path d="M2 6a11 11 0 0 1 16 0M5 9a7 7 0 0 1 10 0M8 12a3 3 0 0 1 4 0" fill="none" stroke="#fff" stroke-width="2" stroke-linecap="round"/>
      </svg>
    </div>
    <div class="clock">4:21 PM</div>
    <div class="battery">
      <span>100%</span>
      <svg width="42" height="18" viewBox="0 0 42 18" aria-hidden="true">
        <rect x="1" y="1" width="36" height="16" rx="3" fill="none" stroke="#fff" stroke-width="1.5"/>
        <rect x="3" y="3" width="32" height="12" rx="1.5" fill="#fff"/>
        <rect x="38.5" y="6" width="2.5" height="6" rx="1" fill="#fff"/>
      </svg>
    </div>
  </div>

  <header class="app-header">
    <svg class="menu-toggle" width="30" height="20" viewBox="0 0 30 20" aria-label="Menu">
      <path d="M1 2H29M1 10H29M1 18H29" stroke="#fff" stroke-width="2.4" stroke-linecap="round"/>
    </svg>
    HOME
  </header>

  <section class="card chart-card">
    <nav class="range-tabs">
      <span class="active" style="left:115px">Today</span>
      <span style="left:226px">Yestarday</span>
      <span style="left:357px">This Week</span>
      <span style="left:493px">This Month</span>
    </nav>
    <svg width="629" height="300" viewBox="0 0 629 300" aria-label="Routines by hour">
      <defs>
        <linearGradient id="barFill" x1="0" y1="0" x2="0" y2="1">
          <stop offset="0" stop-color="var(--orange-light)"/>
          <stop offset="1" stop-color="var(--orange)"/>
        </linearGradient>
      </defs>
      <g stroke="#ececec" stroke-width="1">
        <path d="M162 64V264M240 64V264M319 64V264M397 64V264M476 64V264M555 64V264"/>
      </g>
      <path d="M67 264H560M67 64V264" stroke="#cfcfcf" stroke-width="1.2" fill="none"/>
      <text transform="translate(55 110) rotate(-90)" text-anchor="middle" font-size="15" fill="#777" font-family="Roboto, sans-serif">Lorem ipsum</text>
      <path d="M137 264V198a25 25 0 0 1 50 0V264Z" fill="url(#barFill)"/>
      <path d="M294 264V161a25 25 0 0 1 50 0V264Z" fill="url(#barFill)"/>
      <path d="M451 264V235a25 25 0 0 1 50 0V264Z" fill="url(#barFill)"/>
      <g font-size="15" fill="#555" text-anchor="middle" font-family="Roboto, sans-serif">
        <text x="146" y="159">Lorem ipsum</text>
        <text x="303" y="121">Lorem ipsum</text>
        <text x="460" y="194">Lorem ipsum</text>
      </g>
      <g font-size="16" fill="#555" text-anchor="middle" font-family="Roboto, sans-serif">
        <text x="67" y="289">10am</text><text x="146" y="289">11am</text><text x="224" y="289">12pm</text>
        <text x="303" y="289">1pm</text><text x="381" y="289">2pm</text><text x="460" y="289">3pm</text><text x="539" y="289">4pm</text>
      </g>
      <circle cx="15" cy="175" r="26" fill="#e6e6e6"/>
      <path d="M20 164L12 175L20 186" fill="none" stroke="#aaa" stroke-width="2"/>
      <circle cx="614" cy="175" r="26" fill="#e6e6e6"/>
      <path d="M609 164L617 175L609 186" fill="none" stroke="#333" stroke-width="2"/>
    </svg>
    <p class="total-routines">Total Routines: (<em>1</em>/3)</p>
  </section>

  <section class="card history-card">
    <div class="history-head">
      <h2 class="section-title">History</h2>
      <span class="rule"></span>
      <a class="see-more">See More</a>
    </div>
    <ul class="history-list">
      <li class="history-item">
        <svg class="activity-icon" width="53" height="53" viewBox="0 0 53 53" aria-hidden="true"><circle cx="26.5" cy="26.5" r="26.5" fill="var(--orange)"/><g fill="none" stroke="#fff" stroke-width="3" stroke-linecap="round" stroke-linejoin="round"><circle cx="31" cy="15" r="2.5" fill="#fff"/><path d="M20 21L27 19L25 28L31 32L29 38M25 28L19 34L15 33M27 19L31 25L36 25"/></g></svg>
        <p>Lorem ipsum dolor sit amet, consectetur adipiscing elit.</p><time>5m ago</time>
      </li>
      <li class="history-item">
        <svg class="activity-icon" width="53" height="53" viewBox="0 0 53 53" aria-hidden="true"><circle cx="26.5" cy="26.5" r="26.5" fill="var(--orange)"/><g fill="none" stroke="#fff" stroke-width="3" stroke-linecap="round" stroke-linejoin="round"><circle cx="31" cy="15" r="2.5" fill="#fff"/><path d="M20 21L27 19L25 28L31 32L29 38M25 28L19 34L15 33M27 19L31 25L36 25"/></g></svg>
        <p>Lorem ipsum dolor sit amet, consectetur adipiscing elit.</p><time>2h ago</time>
      </li>
      <li class="history-item">
        <svg class="activity-icon" width="53" height="53" viewBox="0 0 53 53" aria-hidden="true"><circle cx="26.5" cy="26.5" r="26.5" fill="var(--orange)"/><g fill="none" stroke="#fff" stroke-width="3" stroke-linecap="round" stroke-linejoin="round"><circle cx="31" cy="15" r="2.5" fill="#fff"/><path d="M20 21L27 19L25 28L31 32L29 38M25 28L19 34L15 33M27 19L31 25L36 25"/></g></svg>
        <p>Lorem ipsum dolor sit amet, consectetur adipiscing elit.</p><time>5h ago</time>
      </li>
      <li class="history-item">
        <svg class="activity-icon" width="53" height="53" viewBox="0 0 53 53" aria-hidden="true"><circle cx="26.5" cy="26.5" r="26.5" fill="var(--orange)"/><g fill="none" stroke="#fff" stroke-width="3" stroke-linecap="round" stroke-linejoin="round"><circle cx="31" cy="15" r="2.5" fill="#fff"/><path d="M20 21L27 19L25 28L31 32L29 38M25 28L19 34L15 33M27 19L31 25L36 25"/></g></svg>
        <p>Lorem ipsum dolor sit amet, consectetur adipiscing elit.</p><time>1d ago</time>
      </li>
      <li class="history-item faded">
        <svg class="activity-icon" width="53" height="53" viewBox="0 0 53 53" aria-hidden="true"><circle cx="26.5" cy="26.5" r="26.5" fill="var(--orange)"/></svg>
        <p>Lorem ipsum dolor sit amet, consectetur adipiscing elit.</p><time>1d ago</time>
      </li>
    </ul>
    <div class="history-fade"></div>
  </section>

  <section class="card sponsors-card">
    <h2 class="section-title">Sponsors</h2>
    <div class="sponsor-row">
      <div class="sponsor-tile"><span class="mark"></span>Stridewell</div>
      <div class="sponsor-tile">ShopBay</div>
      <div class="sponsor-tile">Harborstay</div>
      <div class="sponsor-tile"></div>
    </div>
  </section>
</main>
</body>
</html>
```